Business Card Design

I need a logo and a business card design that can be used for my business stationary, Facebook page and in the future a website. I don't know if I need a large design for brochures and stationery and a small portion of that as the logo or business card design. I probably need some advice about that. My new company is called Willowbank Family Circle. I don't have all of my business contact details available yet, but I want to get the design ready, so that when all this information is available I can get the printing done quickly.I'm a social worker and my business will be providing parenting groups and counselling sessions for parents.I would like the logo and business card to be very feminine and pretty. I want a silhouette image of a Mother and Baby and decorative swirls of flowers/vines/leaves and butterflies.I have found some designs elsewhere that are along the lines of what I am looking for. These images are attached below, but the quality of these attachments is very poor as I photographed them with my phone.My preferred colours would be to use black and white, purple and/or pink, aqua and or blue/green.There are four logo/business card options attached. Logo option 1 - I really like the flower and vine design. Logo option 2 - again I like the flowers and leaf design and the use of colour and the silhouette image of the Mum and Baby; Logo option 3 - I like the butterflies and decorative swirls in this option and Logo option 4 - I think this design is the best for a logo. I love the mother and baby image. I don't like the tree branch and the birds but I like the way the hair has been incorporated into the branch. I prefer the design of the flowers/vine/leaves in the other options.

Industry/Entity Type

Business

Contact Information for Business Card

Company Name:Embrace Attachment ParentingMobile:0417 751 394Email:Currently sourcing - TBAContact Name:Janelle ApplegarthQualifications:Currently sourcing details - TBA

Font styles to use
Script

Colors
33a6d7
85cae6
886aae
6c459b
e667a6
eea4c8

Requirements
Must have
• My project must have an image of a mother and child, slightly encircled by the mother's hair perhaps in a heart shape, and the mother's hair becoming a beautiful filigree design of vine/leaves/flowers and with some butterfly somewhere.
• Can all of the Words be in the same font Attachment Parenting can be slightly smaller.
Nice to have
• I would like to also have a similar vine/leaves/flowers and maybe a butterfly on the opposite side of the card. Maybe the Mother/child image on the top left of the card and the other pattern on the bottom right.
• If possible the use of aqua, purple and pink.

```html
<!DOCTYPE html>
<html lang="en">
<head>
<meta charset="utf-8">
<title>Willowbank Family Circle – Business Card</title>
<link rel="stylesheet" href="https://fonts.googleapis.com/css2?family=Poiret+One&family=Questrial&display=swap">
<style>
  :root {
    --backdrop: #ede7e3;
    --card: #ffffff;
    --pink-strong: #e065a8;
    --pink-mid: #e98cbf;
    --pink-soft: #eea4c8;
    --pink-pale: #f8dcea;
    --shadow: rgba(90, 50, 60, 0.14);
  }
  html, body {
    margin: 0;
    width: 1200px;
    height: 902px;
    overflow: hidden;
    background: var(--backdrop);
  }
  .canvas {
    position: relative;
    width: 1200px;
    height: 902px;
  }
  .card {
    position: absolute;
    left: 50px;
    top: 137px;
    width: 1100px;
    height: 627px;
    background: var(--card);
    box-shadow: 0 6px 24px var(--shadow);
    overflow: hidden;
  }

  /* Brand block */
  .brand {
    position: absolute;
    left: 42px;
    top: 78px;
    width: 400px;
    text-align: center;
  }
  .brand-dot {
    display: block;
    width: 230px;
    height: 230px;
    margin: 0 auto 34px;
    border-radius: 50%;
    background: var(--pink-pale);
  }
  .brand-name {
    margin: 0;
    font-family: "Poiret One", sans-serif;
    font-weight: 400;
    font-size: 54px;
    line-height: 59px;
    color: var(--pink-strong);
  }

  /* Floral ornament area (top right) */
  .floral {
    position: absolute;
    inset: 0;
    pointer-events: none;
  }
  .floral-top {
    position: absolute;
    left: 714px;
    top: 0;
    width: 150px;
    height: 52px;
    border-radius: 0 0 60px 60px / 0 0 40px 40px;
    background: linear-gradient(90deg, var(--pink-pale), var(--pink-soft) 55%, var(--pink-pale));
  }
  .floral-cluster {
    position: absolute;
    right: 0;
    top: 0;
    width: 224px;
    height: 318px;
    border-radius: 0 0 0 78% / 0 0 0 62%;
    background: linear-gradient(200deg, var(--pink-strong) 0%, var(--pink-mid) 30%, var(--pink-soft) 62%, var(--pink-pale) 100%);
  }
  .floral-wing {
    position: absolute;
    right: 0;
    top: 278px;
    width: 60px;
    height: 112px;
    border-radius: 60px 0 0 60px / 56px 0 0 56px;
    background: linear-gradient(160deg, var(--pink-mid), var(--pink-strong));
  }

  /* Contact block */
  .contact {
    position: absolute;
    left: 531px;
    top: 400px;
  }
  .contact-name {
    margin: 0;
    font-family: "Poiret One", sans-serif;
    font-weight: 400;
    font-size: 47px;
    line-height: 52px;
    color: var(--pink-strong);
  }
  .contact-role {
    margin: 6px 0 0;
    font-family: "Questrial", sans-serif;
    font-size: 28px;
    color: var(--pink-soft);
  }
  .contact-lines {
    list-style: none;
    margin: 30px 0 0;
    padding: 0;
    font-family: "Questrial", sans-serif;
    font-size: 30px;
    line-height: 36px;
    color: var(--pink-strong);
  }
  .contact-lines li {
    display: flex;
    align-items: center;
    gap: 12px;
  }
  .contact-icon {
    width: 28px;
    height: 28px;
    flex: none;
  }
</style>
</head>
<body>
<main class="canvas">
  <section class="card">
    <div class="brand">
      <span class="brand-dot"></span>
      <h1 class="brand-name">Willowbank<br>Family<br>Circle</h1>
    </div>

    <div class="floral" role="img" aria-label="Pink floral filigree of swirling vines, leaves and flowers in the top right corner, with a small flourish along the top edge and a butterfly at the right edge">
      <div class="floral-top"></div>
      <div class="floral-cluster"></div>
      <div class="floral-wing"></div>
    </div>

    <div class="contact">
      <h2 class="contact-name">Rosalind Thackeray</h2>
      <p class="contact-role">Currently sourcing details - TBA</p>
      <ul class="contact-lines">
        <li>
          <svg class="contact-icon" viewBox="0 0 28 28" aria-hidden="true">
            <rect width="28" height="28" fill="var(--pink-soft)"/>
            <rect x="9" y="5" width="10" height="18" rx="1.5" fill="none" stroke="#fff" stroke-width="2"/>
            <line x1="11" y1="18" x2="17" y2="18" stroke="#fff" stroke-width="1.5"/>
          </svg>
          <span>0438 260 517</span>
        </li>
        <li>
          <svg class="contact-icon" viewBox="0 0 28 28" aria-hidden="true">
            <rect width="28" height="28" fill="var(--pink-soft)"/>
            <rect x="5" y="8" width="18" height="12" fill="none" stroke="#fff" stroke-width="2"/>
            <polyline points="5,8 14,15 23,8" fill="none" stroke="#fff" stroke-width="2"/>
          </svg>
          <span>Currently sourcing - TBA</span>
        </li>
      </ul>
    </div>
  </section>
</main>
</body>
</html>
```